Set of 6 Illustrations for Transport Security Platform – Duvrelt

Duvrelt is an innovative solution that enhances safety in transport and logistics, based on identity verification, access control, and collaboration within a network of verified subcontractors.
The purpose of the graphics is to present the system’s key functionalities in a modern, technological way that aligns with the brand’s visual identity.
The website will feature a clean and bright aesthetic:
Background: white or light gray (#f7f7f7)
Text: black or dark gray (#1a1a1a)
Accent color: green (#27ae60 or #2ecc71) – symbolizing safety and trust
The graphics should be stylistically consistent, simple, and easy to read — ideally created in a flat design or isometric 3D style with subtle gradients.
We should avoid stock photos of people or trucks — the goal is a symbolic and technological visual approach.
I initially prepared the graphics myself in Canva, but they are not visually consistent.
Colors
Designer to choose only greyscale colors for use in the design.
Look and feel
Each slider illustrates characteristics of the customer's brand and the style your logo design should communicate.

```html
<!DOCTYPE html>
<html lang="en">
<head>
<meta charset="utf-8">
<title>Duvrelt – verification flow</title>
<link rel="stylesheet" href="https://fonts.googleapis.com/css2?family=Raleway:wght@400;600;700;800&family=Oswald:wght@500;600&display=swap">
<style>
:root{
  --green:#24ae5f;
  --green-soft:#7dc47f;
  --green-pill:#6cc07a;
  --stage:#eeeeee;
  --pill-grey:#e2e8e2;
  --ink:#1a1a1a;
  --ink-soft:#333333;
  --white:#ffffff;
}
*{box-sizing:border-box;margin:0;padding:0}
html,body{width:1200px;height:793px;overflow:hidden;background:var(--white)}
body{font-family:"Raleway",Arial,sans-serif;color:var(--ink);position:relative}
.stage{position:absolute;left:0;top:87px;width:867px;height:676px;background:var(--stage);border-radius:78px}
.connectors{position:absolute;left:0;top:0;width:1200px;height:793px}
.connectors path{fill:none;stroke:var(--green-soft);stroke-width:16;stroke-linejoin:round;stroke-linecap:butt}
.card{position:absolute;background:var(--white);border:3px solid var(--green);border-radius:12px}
.abs{position:absolute}
.title-step{font-weight:800;font-size:18px;letter-spacing:.2px}
.btn{position:absolute;background:var(--green);color:var(--white);display:flex;align-items:center;justify-content:center;border-radius:20px;font-weight:700}
.details{position:absolute;right:10px;bottom:-3px;width:84px;height:29px;background:var(--green);border-radius:15px 15px 8px 8px;color:var(--white);font-family:"Oswald",sans-serif;font-weight:500;font-size:16px;display:flex;align-items:center;justify-content:center;gap:5px;letter-spacing:.3px}
.details .dots{width:13px;height:13px;border-radius:50%;background:var(--white);position:relative}
.details .dots::after{content:"";position:absolute;left:3px;top:5px;width:7px;height:2px;background:repeating-linear-gradient(90deg,var(--green) 0 1.6px,transparent 1.6px 2.8px)}
.stamp{position:absolute;font-family:"Oswald",sans-serif;font-weight:500;font-size:16px;line-height:1;color:var(--green);padding:6px 7px}
.stamp::before,.stamp::after{content:"";position:absolute;top:0;bottom:0;width:7px;border:3px solid currentColor}
.stamp::before{left:0;border-right:none;border-radius:4px 0 0 4px}
.stamp::after{right:0;border-left:none;border-radius:0 4px 4px 0}
.stamp.rejected{color:#3a3a3a}
.tick{position:absolute;width:22px;height:22px}
.name{position:absolute;font-weight:700;font-size:13px;letter-spacing:-.2px;white-space:nowrap}
.figure{position:absolute;background:linear-gradient(180deg,#2fb869,var(--green));border-radius:34px 34px 6px 6px}
.start-tab{position:absolute;left:113px;top:166px;width:83px;height:32px;background:var(--green);color:var(--white);border-radius:14px 14px 0 0;font-weight:700;font-size:13px;text-align:center;padding-top:9px}
.check-panel{position:absolute;left:57px;top:420px;width:195px;height:261px;background:var(--green);border-radius:26px}
.check-head{position:absolute;left:8px;top:10px;width:178px;height:39px;background:var(--white);border-radius:18px;display:flex;align-items:center;justify-content:center;font-weight:700;font-size:15px}
.check-item{position:absolute;left:20px;display:flex;align-items:center;gap:11px;color:var(--white);font-weight:700;font-size:15px;line-height:15px}
.check-item svg{width:34px;height:34px;flex:none}
.detail-row{position:absolute;left:34px;font-size:14px;line-height:1.2}
.detail-row b{font-weight:700}
.detail-row .val{font-weight:400;font-size:14px}
.tag{position:absolute;left:8px;height:20px;border-radius:5px;font-weight:700;font-size:14px;padding:0 5px;display:flex;align-items:center}
.need{position:absolute;left:8px;width:178px;height:40px;background:var(--pill-grey);border-radius:18px;display:flex;align-items:center;justify-content:center;text-align:center;font-weight:700;font-size:14px;line-height:15px}
.pass{position:absolute;left:907px;top:607px;width:293px;height:186px;background:var(--green);border-radius:26px 0 0 0;color:var(--white)}
.pass .stamp{color:var(--white);font-size:24px;padding:6px 9px}
.pass-lines{position:absolute;left:13px;top:66px;font-size:14.5px;line-height:18.3px;color:var(--white)}
.pass-lines b{color:var(--ink);font-weight:700}
.idcard{position:absolute;left:189px;top:111px;width:88px;height:60px;background:var(--white);border-radius:4px}
</style>
</head>
<body>

<div class="stage"></div>

<svg class="connectors" viewBox="0 0 1200 793" aria-hidden="true">
  <path d="M251 263 H277 Q291 263 291 277 V491 Q291 505 305 505 H336"/>
  <path d="M430 357 V398"/>
  <path d="M430 377 H557 Q575 377 575 359 V297 Q575 283 589 283 H618"/>
  <path d="M430 535 V567"/>
  <path d="M532 510 H562 Q576 510 576 496 V430 Q576 416 590 416 H618"/>
  <path d="M813 392 H847 Q863 392 863 408 V469 Q863 483 877 483 H908"/>
  <path d="M1001 286 V352"/>
  <path d="M1053 543 V608"/>
</svg>

<!-- Step 1 -->
<div class="start-tab">Start</div>
<section class="card step-one" style="left:56px;top:195px;width:196px;height:161px;border-radius:22px">
  <div class="abs title-step" style="left:17px;top:15px">Step 1</div>
  <svg class="abs" style="left:66px;top:60px" width="62" height="33" viewBox="0 0 62 33" aria-hidden="true">
    <path d="M0 8 L22 0 L44 8 V12 H49 V6 H56 V12 H62 V33 H0Z" fill="var(--green)"/>
    <rect x="6" y="14" width="9" height="7" fill="#fff"/><rect x="19" y="14" width="9" height="7" fill="#fff"/><rect x="32" y="14" width="9" height="7" fill="#fff"/>
  </svg>
  <div class="btn" style="left:6px;top:110px;width:179px;height:40px;font-size:14.5px;gap:8px">COMPANY FINDER
    <svg width="18" height="20" viewBox="0 0 18 20" aria-hidden="true"><circle cx="7" cy="7" r="5.5" fill="none" stroke="#fff" stroke-width="2"/><path d="M11 11 L16 18" stroke="#fff" stroke-width="2.2" stroke-linecap="round"/></svg>
  </div>
</section>

<!-- Company check -->
<section class="check-panel">
  <div class="check-head">Company Check</div>
  <div class="check-item" style="top:64px">
    <svg viewBox="0 0 34 34" aria-hidden="true"><circle cx="17" cy="17" r="17" fill="#fff"/><path d="M9 17 L15 23 L26 11" fill="none" stroke="var(--green)" stroke-width="4.5" stroke-linecap="round" stroke-linejoin="round"/></svg>
    <span style="margin-left:6px">Active</span>
  </div>
  <div class="check-item" style="top:106px">
    <svg viewBox="0 0 34 34" aria-hidden="true"><circle cx="17" cy="17" r="17" fill="#fff"/><path d="M9 17 L15 23 L26 11" fill="none" stroke="var(--green)" stroke-width="4.5" stroke-linecap="round" stroke-linejoin="round"/></svg>
    <span>Company<br>verified</span>
  </div>
  <div class="check-item" style="top:150px">
    <svg viewBox="0 0 34 34" aria-hidden="true"><circle cx="17" cy="17" r="17" fill="#fff"/><path d="M9 17 L15 23 L26 11" fill="none" stroke="var(--green)" stroke-width="4.5" stroke-linecap="round" stroke-linejoin="round"/></svg>
    <span>Verified<br>employee</span>
  </div>
  <div class="check-item" style="top:197px">
    <svg viewBox="0 0 34 34" aria-hidden="true" fill="#fff">
      <circle cx="9" cy="7" r="3.6"/><circle cx="17" cy="3.5" r="3"/><circle cx="25" cy="6" r="2.6"/><circle cx="29" cy="13" r="2.2"/><circle cx="28" cy="21" r="1.8"/><circle cx="23" cy="28" r="1.4"/><circle cx="16" cy="30" r="1.1"/><circle cx="9" cy="27" r="1"/><circle cx="5" cy="20" r="1"/><circle cx="4.5" cy="13" r="1.6"/>
    </svg>
    <span>Number of<br>verified drivers</span>
  </div>
</section>

<!-- Driver approved -->
<section class="card" style="left:335px;top:218px;width:198px;height:141px">
  <div class="stamp" style="left:15px;top:17px">APPROVED</div>
  <svg class="tick" style="left:98px;top:26px" viewBox="0 0 22 22" aria-hidden="true"><path d="M2 12 L8 18 L20 4" fill="none" stroke="var(--green)" stroke-width="3.5" stroke-linecap="round"/></svg>
  <div class="name" style="left:11px;top:60px">Tomas Verhaal</div>
  <div class="figure" role="img" aria-label="Illustration of a truck driver in a cap" style="left:124px;top:14px;width:66px;height:89px"></div>
  <div class="details"><span class="dots"></span>DETAILS</div>
</section>

<!-- Company data approved -->
<section class="card" style="left:335px;top:397px;width:198px;height:140px">
  <div class="stamp" style="left:15px;top:17px">APPROVED</div>
  <svg class="tick" style="left:98px;top:26px" viewBox="0 0 22 22" aria-hidden="true"><path d="M2 12 L8 18 L20 4" fill="none" stroke="var(--green)" stroke-width="3.5" stroke-linecap="round"/></svg>
  <svg class="abs" style="left:124px;top:19px" width="62" height="31" viewBox="0 0 62 31" aria-hidden="true">
    <path d="M0 8 L22 0 L44 8 V10 H49 V4 H56 V10 H62 V31 H0Z" fill="var(--green)"/>
    <rect x="6" y="13" width="9" height="7" fill="#fff"/><rect x="19" y="13" width="9" height="7" fill="#fff"/><rect x="32" y="13" width="9" height="7" fill="#fff"/>
  </svg>
  <svg class="abs" style="left:146px;top:60px" width="44" height="21" viewBox="0 0 64 30" aria-hidden="true">
    <rect x="18" y="0" width="46" height="19" fill="var(--green)"/>
    <path d="M2 12 L6 5 H16 V22 H2Z" fill="none" stroke="var(--green)" stroke-width="2.5"/>
    <rect x="0" y="21" width="62" height="3" fill="var(--green)"/>
    <circle cx="9" cy="25" r="4.5" fill="var(--green)"/><circle cx="44" cy="25" r="4.5" fill="var(--green)"/>
  </svg>
  <div class="name" style="left:10px;top:70px;font-size:12px">Norvane Haulage LTD</div>
  <div class="abs" style="left:12px;top:87px;color:var(--green);font-weight:700;font-size:12.5px">COMPANY DATA</div>
  <div class="details"><span class="dots"></span>DETAILS</div>
</section>

<!-- Drivers count -->
<section class="card" style="left:335px;top:566px;width:198px;height:141px">
  <div class="stamp" style="left:15px;top:17px">APPROVED</div>
  <svg class="tick" style="left:98px;top:26px" viewBox="0 0 22 22" aria-hidden="true"><path d="M2 12 L8 18 L20 4" fill="none" stroke="var(--green)" stroke-width="3.5" stroke-linecap="round"/></svg>
  <div class="name" style="left:13px;top:63px;font-size:14.5px">Number of drivers:</div>
  <div class="abs" style="left:38px;top:84px;color:var(--green);font-family:'Oswald',sans-serif;font-weight:600;font-size:32px;line-height:1">35</div>
  <div class="details" style="right:12px"><span class="dots"></span>DETAILS</div>
</section>

<!-- Rejected driver -->
<section class="card" style="left:617px;top:176px;width:198px;height:141px">
  <div class="stamp rejected" style="left:18px;top:17px">REJECTED</div>
  <svg class="abs" style="left:103px;top:29px" width="16" height="16" viewBox="0 0 16 16" aria-hidden="true"><path d="M2 2 L14 14 M14 2 L2 14" stroke="#222" stroke-width="3.4" stroke-linecap="round"/></svg>
  <div class="name" style="left:18px;top:58px;font-size:13.5px">Mira Solberg</div>
  <div class="figure" role="img" aria-label="Illustration of a woman driver" style="left:126px;top:20px;width:60px;height:84px"></div>
  <div class="details" style="right:6px"><span class="dots"></span>DETAILS</div>
</section>

<!-- Company detail -->
<section class="card" style="left:617px;top:378px;width:198px;height:286px">
  <svg class="abs" style="left:66px;top:15px" width="62" height="31" viewBox="0 0 62 31" aria-hidden="true">
    <path d="M0 8 L22 0 L44 8 V10 H49 V4 H56 V10 H62 V31 H0Z" fill="var(--green)"/>
    <rect x="6" y="13" width="9" height="7" fill="#fff"/><rect x="19" y="13" width="9" height="7" fill="#fff"/><rect x="32" y="13" width="9" height="7" fill="#fff"/>
  </svg>
  <div class="name" style="left:0;width:192px;text-align:center;top:58px;font-size:13.5px">Norvane Haulage LTD</div>
  <div class="detail-row" style="left:32px;top:92px"><b>Vat No.</b> <span class="val">512870346</span></div>
  <div class="detail-row" style="left:32px;top:121px"><b>Verified phone no.:</b><br><span class="val">+32 470 118 262</span></div>
  <div class="detail-row" style="left:33px;top:170px"><b>Verified bank No.:</b><br><span class="val">BE910274381556</span></div>
  <div class="btn" style="left:8px;top:232px;width:178px;height:40px;font-size:13.5px;letter-spacing:-.3px">ADD TO THE NETWORK +</div>
</section>

<!-- Conditions -->
<section class="card" style="left:905px;top:2px;width:198px;height:286px;border-radius:14px">
  <div class="abs" style="left:11px;top:18px;font-weight:700;font-size:15px">Conditions</div>
  <div class="tag" style="top:36px;background:var(--green-pill);font-size:15px">Location 1</div>
  <svg class="abs" style="left:151px;top:12px" width="30" height="45" viewBox="0 0 30 45" aria-hidden="true"><path d="M15 0 C6.7 0 0 6.7 0 15 C0 26 15 45 15 45 C15 45 30 26 30 15 C30 6.7 23.3 0 15 0Z" fill="var(--green)"/><circle cx="15" cy="15" r="5.5" fill="#fff"/></svg>
  <div class="tag" style="top:79px;height:22px;background:var(--green);color:var(--white);font-size:15px">Plant 1</div>
  <div class="need" style="top:124px">Active geofencing<br>required</div>
  <div class="need" style="top:181px">Verified identity<br>required</div>
  <div class="btn" style="left:54px;top:252px;width:83px;height:33px;border-radius:16px 16px 0 0;font-family:'Oswald',sans-serif;font-weight:500;font-size:17px;gap:8px">NEXT
    <svg width="10" height="12" viewBox="0 0 10 12" aria-hidden="true"><path d="M0 0 L10 6 L0 12Z" fill="#fff"/></svg>
  </div>
</section>

<!-- Step 2 -->
<section class="card" style="left:907px;top:351px;width:196px;height:194px;border-radius:22px">
  <div class="abs title-step" style="left:14px;top:6px">Step 2</div>
  <div class="abs" style="left:0;width:190px;text-align:center;top:32px;font-weight:700;font-size:14.5px">Gate portal</div>
  <svg class="abs" style="left:65px;top:57px" width="62" height="31" viewBox="0 0 62 31" aria-hidden="true">
    <path d="M0 8 L22 0 L44 8 V10 H49 V4 H56 V10 H62 V31 H0Z" fill="var(--green)"/>
    <rect x="6" y="13" width="9" height="7" fill="#fff"/><rect x="19" y="13" width="9" height="7" fill="#fff"/><rect x="32" y="13" width="9" height="7" fill="#fff"/>
  </svg>
  <div class="abs" style="left:6px;top:93px;width:179px;height:41px;border:3px solid var(--green);border-radius:20px;display:flex;align-items:center;justify-content:center;color:var(--green);font-weight:700;font-size:14px">
    <svg class="abs" style="left:12px;top:6px" width="18" height="25" viewBox="0 0 30 45" aria-hidden="true"><path d="M15 0 C6.7 0 0 6.7 0 15 C0 26 15 45 15 45 C15 45 30 26 30 15 C30 6.7 23.3 0 15 0Z" fill="var(--green)"/><circle cx="15" cy="15" r="6" fill="#fff"/></svg>
    PLANT 1
  </div>
  <div class="btn" style="left:6px;top:143px;width:179px;height:40px;font-size:14px">VERIFIER
    <svg class="abs" style="right:18px;top:13px" width="11" height="14" viewBox="0 0 11 14" aria-hidden="true"><path d="M0 0 L11 7 L0 14Z" fill="#fff"/></svg>
  </div>
</section>

<!-- Gate pass -->
<section class="pass">
  <div class="stamp" style="left:15px;top:13px">APPROVED</div>
  <svg class="abs" style="left:192px;top:19px" width="23" height="33" viewBox="0 0 30 45" aria-hidden="true"><path d="M15 0 C6.7 0 0 6.7 0 15 C0 26 15 45 15 45 C15 45 30 26 30 15 C30 6.7 23.3 0 15 0Z" fill="#fff"/><circle cx="15" cy="15" r="6" fill="var(--green)"/></svg>
  <div class="abs" style="left:191px;top:55px;font-family:'Oswald',sans-serif;font-size:11px;font-weight:500">GPS</div>
  <div class="pass-lines">
    <div><b>Driver:</b> Tomas Verhaal</div>
    <div><b>Company:</b> Norvane Haulage LTD</div>
    <div><b>Truck:</b> KTR4PL81</div>
    <div><b>Truck:</b> Marlow</div>
    <div><b>Truck color:</b> White</div>
  </div>
  <div class="idcard">
    <div class="abs" style="left:0;width:88px;top:3px;text-align:center;color:var(--green);font-weight:700;font-size:10px">ID CARD</div>
    <div class="abs" role="img" aria-label="Portrait area of the ID card" style="left:6px;top:19px;width:28px;height:34px;background:var(--green);border-radius:2px"></div>
    <svg class="abs" style="left:39px;top:20px" width="44" height="34" viewBox="0 0 44 34" aria-hidden="true" fill="var(--green)">
      <rect x="0" y="0" width="12" height="3"/><rect x="15" y="0" width="28" height="3"/>
      <rect x="0" y="7" width="43" height="3"/><rect x="0" y="14" width="30" height="3"/>
      <rect x="0" y="21" width="20" height="3"/><rect x="30" y="20" width="14" height="12" rx="1"/>
    </svg>
    <div class="abs" style="left:71px;top:42px;color:#fff;font-size:7px;font-weight:800">ES</div>
  </div>
</section>

</body>
</html>
```